stationary deign for trucking company

im a trucking company looking for a professional set of stationary designs i deliver goods from point a to b
Updates

When submitting stationary designs I need envelope design, letterhead, cards, I’d badge etc

Industry/Entity Type

Trucking Company

Requirements
Must have
• must have letter head, business card, envelope, fax sheet, id badge, folder, thank you card, notebook, invoice sheet.
Nice to have
• nice to have them all custom made (letterhead,envelope, business card, I’d badge etc
Should not have
• must not have prepaid sign want i unique design for items

```html
<!DOCTYPE html>
<html lang="en">
<head>
<meta charset="utf-8">
<title>Harlow Freight – Employee ID Badge</title>
<link href="https://fonts.googleapis.com/css2?family=Arimo:wght@400;700&display=swap" rel="stylesheet">
<style>
  :root {
    --brand-blue: #1a5ca8;
    --brand-blue-soft: #8fb0d8;
    --band-grey: #e7e8ea;
    --ink: #111111;
    --paper: #ffffff;
    --photo-dark: #08090a;
  }
  * { margin: 0; padding: 0; box-sizing: border-box; }
  html, body {
    width: 1200px;
    height: 1200px;
    overflow: hidden;
    background: var(--paper);
    font-family: "Arimo", Arial, sans-serif;
  }
  .badge {
    position: absolute;
    left: 345px;
    top: 195px;
    width: 510px;
    height: 810px;
    overflow: hidden;
    background: var(--paper);
  }
  .badge-graphics {
    position: absolute;
    inset: 0;
    width: 510px;
    height: 810px;
  }
  .company-name {
    position: absolute;
    left: 0;
    top: 38px;
    width: 510px;
    height: 100px;
    display: flex;
    align-items: center;
    justify-content: center;
    font-weight: 700;
    font-size: 34px;
    letter-spacing: 3px;
    color: var(--ink);
  }
  .employee-name {
    position: absolute;
    left: 119px;
    top: 421px;
    width: 273px;
    height: 35px;
    border-radius: 18px;
    background: var(--brand-blue);
    color: var(--paper);
    font-weight: 700;
    font-size: 29px;
    line-height: 35px;
    text-align: center;
  }
  .designation {
    position: absolute;
    left: 0;
    width: 510px;
    top: 454px;
    text-align: center;
    font-size: 21px;
    line-height: 24px;
    color: var(--brand-blue);
  }
  .detail { position: absolute; }
  .detail-label {
    font-weight: 700;
    font-size: 22px;
    line-height: 26px;
    color: var(--brand-blue);
  }
  .detail-value {
    margin-top: 6px;
    font-size: 13px;
    line-height: 16px;
    color: var(--ink);
  }
  .col-left { left: 90px; }
  .col-right { left: 293px; }
  .row-1 { top: 541px; }
  .row-2 { top: 610px; }
  .row-3 { top: 689px; }
  .website {
    position: absolute;
    left: 0;
    width: 510px;
    top: 760px;
    text-align: center;
    font-size: 22px;
    color: var(--brand-blue);
  }
</style>
</head>
<body>
  <main class="badge">
    <svg class="badge-graphics" viewBox="0 0 637 1012" preserveAspectRatio="none" aria-hidden="true">
      <defs>
        <linearGradient id="decor-fade" x1="0" y1="0" x2="0" y2="1">
          <stop offset="0" stop-color="var(--brand-blue)"/>
          <stop offset="0.6" stop-color="var(--brand-blue-soft)"/>
          <stop offset="1" stop-color="var(--paper)"/>
        </linearGradient>
      </defs>
      <rect class="top-band" x="0" y="0" width="637" height="47" fill="var(--brand-blue)"/>
      <rect class="header-band" x="0" y="47" width="637" height="125" fill="var(--band-grey)"/>
    </svg>
    <svg class="badge-graphics" viewBox="0 0 637 1012" preserveAspectRatio="none" role="img" aria-label="Decorative blue background area">
      <rect class="decor-area" x="0" y="172" width="637" height="345" fill="url(#decor-fade)"/>
    </svg>
    <svg class="badge-graphics" viewBox="0 0 637 1012" preserveAspectRatio="none" aria-hidden="true">
      <circle class="photo-frame" cx="319" cy="373" r="134" fill="var(--paper)" stroke="var(--ink)" stroke-width="3"/>
    </svg>
    <svg class="badge-graphics" viewBox="0 0 637 1012" preserveAspectRatio="none" role="img" aria-label="Employee photo">
      <circle class="photo" cx="319" cy="373" r="110" fill="var(--photo-dark)"/>
    </svg>

    <div class="company-name">HARLOW FREIGHT</div>

    <div class="employee-name">EMPLOYE NAME</div>
    <div class="designation">designation</div>

    <div class="detail col-left row-1"><div class="detail-label">D.O.B</div><div class="detail-value">01.01.2019</div></div>
    <div class="detail col-right row-1"><div class="detail-label">Id No</div><div class="detail-value">012345</div></div>
    <div class="detail col-left row-2"><div class="detail-label">Joined Date</div><div class="detail-value">01.01.2017</div></div>
    <div class="detail col-right row-2"><div class="detail-label">Expiry Date</div><div class="detail-value">01.01.2022</div></div>
    <div class="detail col-left row-3"><div class="detail-label">Email</div><div class="detail-value">info@harlowmail.com</div></div>
    <div class="detail col-right row-3"><div class="detail-label">Phone</div><div class="detail-value">555014728</div></div>

    <div class="website">harlowfreight.com</div>
  </main>
</body>
</html>
```